Letterhead for a German Distribution/Manufacturing Company

We need a professional Letterhead in a unique Design.
not to playful.
The Letterhead has to show show that we are a international company with headquater in Germany.
all details like adress, Vat Tax Number, Bank Accout, Eori, email, Company number has to be on the Letterhead.
for example use: VAT TAX DE5470318 Bank Account: Kestrel Bank IBAN DE412058731ß204683 Swift: MORV0417352 EORI 3150428697 Company Number: HRB 51806 Adress: VOLMINTA UG Ahornweg 7 Postal Code 06384 City Wendelsau Country: Germany Email: info@volminta-example.com
the design can be colored but doesnt have to be
Industry/Entity Type
Manufacturing and international distribution
Requirements
Must have
- show that we are a international company with headquater in Germany. our company infos and logo

```html
<!DOCTYPE html>
<html lang="en">
<head>
<meta charset="utf-8">
<title>VOLMINTA Letterhead</title>
<link rel="stylesheet" href="https://fonts.googleapis.com/css2?family=Poppins:wght@400;500;600&display=swap">
<style>
:root{
  --backdrop:#ececec;
  --paper:#ffffff;
  --ink:#2b2b2b;
  --ink-soft:#444444;
  --accent-red:#e0434e;
  --accent-purple:#7a3fa0;
  --footer-bg:#2b2b2b;
  --footer-text:#ffffff;
  --icon-grey:#b5b5b5;
  --flag-black:#1b1b1b;
  --flag-red:#d7262e;
  --flag-gold:#f2b713;
}
*{margin:0;padding:0;box-sizing:border-box}
html,body{width:1200px;height:2400px;overflow:hidden;background:var(--backdrop)}
body{position:relative;font-family:'Poppins',sans-serif;color:var(--ink)}
.letterhead{
  position:absolute;left:50px;top:490px;
  width:1022px;height:1320px;
  background:var(--paper);
  transform:scale(1.0763);transform-origin:top left;
  box-shadow:0 6px 28px rgba(0,0,0,.18);
  overflow:hidden;
}
.edge-band{
  position:absolute;left:0;top:0;width:27px;height:100%;
  background:linear-gradient(to bottom,#e6e6e6 0%,#9a9a9a 35%,#2a2a2a 100%);
}
.brand{
  position:absolute;left:76px;top:68px;
  display:flex;align-items:center;gap:18px;
}
.brand-dot{width:62px;height:62px;border-radius:50%;background:var(--ink-soft)}
.brand-name{font-size:52px;font-weight:400;color:var(--ink-soft);letter-spacing:1px;line-height:1}
.hq-block{
  position:absolute;left:647px;top:55px;
  padding-left:26px;
}
.hq-block::before{
  content:"";position:absolute;left:0;top:0;width:2px;height:178px;
  background:linear-gradient(to bottom,var(--accent-purple),var(--accent-red));
}
.hq-title{display:flex;align-items:flex-start;gap:10px}
.hq-title svg{margin-top:2px}
.hq-title p{font-size:16.5px;font-weight:600;color:var(--accent-red);line-height:20px;text-transform:uppercase}
.hq-row{display:flex;align-items:flex-start;gap:12px;font-size:15.5px;line-height:18px;color:var(--ink);margin-left:2px}
.hq-row.address{margin-top:20px}
.hq-row.email{margin-top:17px}
.hq-row.web{margin-top:12px}
.letter{
  position:absolute;left:74px;top:345px;width:862px;
  font-size:18.5px;line-height:25px;color:var(--ink);
}
.recipient{margin-bottom:25px}
.letter .gap{margin-top:25px}
.signature{
  width:190px;height:50px;margin-top:10px;
  background:linear-gradient(90deg,#e8e8e8,#f4f4f4);border-radius:4px;
}
.legal-footer{
  position:absolute;left:205px;bottom:0;width:817px;height:120px;
  background:var(--footer-bg);color:var(--footer-text);
  font-size:14.5px;line-height:18px;
}
.legal-footer strong{font-weight:600}
.legal-col{position:absolute;top:18px}
.legal-col.left{left:45px}
.legal-col.right{left:454px}
.legal-col p+p{margin-top:10px}
.legal-col.left p+p{margin-top:8px}
</style>
</head>
<body>
<main class="letterhead">
  <div class="edge-band"></div>

  <header class="brand">
    <span class="brand-dot"></span>
    <span class="brand-name">VOLMINTA</span>
  </header>

  <section class="hq-block">
    <div class="hq-title">
      <svg width="36" height="38" viewBox="0 0 36 38" aria-hidden="true">
        <rect x="2" y="2" width="2.5" height="34" fill="var(--flag-black)"/>
        <rect x="5" y="4" width="28" height="8" fill="var(--flag-black)"/>
        <rect x="5" y="12" width="28" height="8" fill="var(--flag-red)"/>
        <rect x="5" y="20" width="28" height="8" fill="var(--flag-gold)"/>
      </svg>
      <p>International company<br>headquarter in Germany</p>
    </div>
    <div class="hq-row address">
      <svg width="18" height="22" viewBox="0 0 18 22" aria-hidden="true"><path d="M9 1a7 7 0 0 0-7 7c0 5 7 12 7 12s7-7 7-12a7 7 0 0 0-7-7z" fill="none" stroke="var(--icon-grey)" stroke-width="1.6"/><circle cx="9" cy="8" r="2.5" fill="var(--icon-grey)"/></svg>
      <span>VOLMINTA UG Ahornweg 7<br>Postal Code 06384<br>City Wendelsau Country,Germany</span>
    </div>
    <div class="hq-row email">
      <svg width="18" height="14" viewBox="0 0 18 14" aria-hidden="true"><rect x="1" y="1" width="16" height="12" fill="none" stroke="var(--icon-grey)" stroke-width="1.6"/><path d="M1 1l8 7 8-7" fill="none" stroke="var(--icon-grey)" stroke-width="1.6"/></svg>
      <span>info@volminta-example.com</span>
    </div>
    <div class="hq-row web">
      <svg width="18" height="18" viewBox="0 0 18 18" aria-hidden="true"><circle cx="9" cy="9" r="8" fill="none" stroke="var(--icon-grey)" stroke-width="1.5"/><ellipse cx="9" cy="9" rx="3.5" ry="8" fill="none" stroke="var(--icon-grey)" stroke-width="1.2"/><path d="M1 9h16M2.5 5h13M2.5 13h13" stroke="var(--icon-grey)" stroke-width="1.2"/></svg>
      <span>www.volminta-example.com</span>
    </div>
  </section>

  <article class="letter">
    <div class="recipient">
      <p>To</p>
      <p>Name of the Recipient</p>
      <p>Designation</p>
      <p>Compnay Name</p>
      <p>Address</p>
      <p>Subject:</p>
    </div>
    <p>Dear Mr/Ms.</p>
    <p>I would like to inform you that I am resigning from your position as [Name of the Designation] for the [Name of the Company], effective from [Date &amp; Year].</p>
    <p>Thank you for the support and the opportunitites that you have provided me during the last [Number of Year] years. I have truly enjoyed my tenure with [Name of the Company], and am more than grateful for the encouragement you have given me in pursuing my professional goals and personal growth objectives.</p>
    <p class="gap">If I can be of any assistance during this transition in order to faciliatate the seamless passing of my responsibilities to my successor, please let me know. I would be glas to help however I can.</p>
    <p class="gap">Yours Sincerely,</p>
    <p>Name</p>
    <div class="signature" role="img" aria-label="Handwritten signature"></div>
  </article>

  <footer class="legal-footer">
    <div class="legal-col left">
      <p><strong>VAT TAX:</strong> DE5470318</p>
      <p><strong>BANK ACCOUNT:</strong><br>Kestrel Bank IBAN DE412058731ß204683</p>
    </div>
    <div class="legal-col right">
      <p><strong>SWIFT:</strong> MORV0417352 EORI 3150428697</p>
      <p><strong>COMPANY NUMBER:</strong> HRB 51806</p>
    </div>
  </footer>
</main>
</body>
</html>
```